Simple landing page for Brambles cookbook

I need a one page landingpage where customers can order the cookbook.
This is a cookbook of a collection of recipes from our deli that we used to run.
I need a landing page where customers can come and order the book. I also need it coded. I already have the domain through hostwell.
I can send the file of the book through wetransfer. It's too big to upload here. Just so you get the feel that I am looking for.
I attached a simple text as an introduction to the page. But I am open to any suggestions. I want it all to be about the experience that we are sharing the recipes with everybody and that it's for sale. The book is $29.99, shipping included.
Customers have to be able to click and buy the book from it.

Coding

Coded - Design and coding required

Number of Pages Required

1 page

Font styles to use
Sans Serif

Requirements
Must have
• Same colors as the cookbook

```html
<!DOCTYPE html>
<html lang="en">
<head>
<meta charset="utf-8">
<title>Brambles Cookbook</title>
<link href="https://fonts.googleapis.com/css2?family=Kalam:wght@700&family=Lato:wght@400;700;900&family=Roboto:wght@700&display=swap" rel="stylesheet">
<style>
:root{
  --pink:#d81b5a;
  --ink:#1b1620;
  --night:#1a1320;
  --white:#ffffff;
  --text:#2b2b2b;
  --wood-dark:#2e2420;
  --wood-mid:#6b4a32;
}
*{margin:0;padding:0;box-sizing:border-box}
html,body{width:726px;height:1200px;overflow:hidden;background:var(--white)}
body{position:relative;font-family:'Lato',sans-serif;color:var(--text)}
.hero{position:absolute;left:0;top:0;width:726px;height:435px;
  background:radial-gradient(ellipse at 50% 45%,#9a6a3e 0%,var(--wood-mid) 35%,var(--wood-dark) 75%,#1c1714 100%)}
.hero-edge{position:absolute;left:0;top:360px;width:726px;height:80px}
.header{position:absolute;left:0;top:0;width:726px;height:60px}
.brand{position:absolute;left:66px;top:12px;font:900 26px/1 'Lato',sans-serif;color:var(--white);letter-spacing:1px;text-transform:uppercase}
.nav{position:absolute;top:23px;left:354px;display:flex;gap:20px;font:700 9.5px/1 'Roboto',sans-serif;text-transform:uppercase}
.nav a{color:var(--white);text-decoration:none}
.nav a.active{color:var(--pink)}
.call{position:absolute;left:529px;top:16px;display:flex;align-items:center;gap:8px;color:var(--white);font-family:'Roboto',sans-serif}
.call small{display:block;font-size:9px;font-weight:700}
.call strong{display:block;font-size:12.5px;margin-top:2px}
.hero-title{position:absolute;left:0;width:726px;top:122px;text-align:center;font:700 52px/0.98 'Kalam',cursive;color:var(--white)}
.arrow{position:absolute;top:177px}
.arrow.prev{left:40px}.arrow.next{left:655px}

.intro{position:absolute;left:69px;top:470px;width:330px}
.intro h1{font:700 32px/1 'Kalam',cursive;color:var(--ink);margin-left:0}
.intro h1 span{color:var(--pink)}
.points{list-style:none;margin-top:25px}
.points li{position:relative;padding-left:14px;font-size:9px;line-height:15.6px;text-align:justify;margin-bottom:15.5px}
.points li::before{content:"";position:absolute;left:-1px;top:3px;width:8px;height:8px;border:1.6px solid var(--pink);border-radius:50%}
.buy{position:absolute;left:67px;top:874px;width:85px;height:27px;border-radius:14px;background:var(--pink);color:var(--white);font:900 9.5px/27px 'Lato',sans-serif;text-align:center;text-decoration:none;text-transform:uppercase}
.book-art{position:absolute;left:420px;top:480px;width:306px;height:400px}

.footer-art{position:absolute;left:0;top:0;width:726px;height:1200px;pointer-events:none}
.footer-brand{position:absolute;left:0;width:726px;top:964px;text-align:center;font:900 26px/1 'Lato',sans-serif;color:var(--white);letter-spacing:1px;text-transform:uppercase}
.contacts{position:absolute;left:0;top:1016px;width:726px}
.contact{position:absolute;width:200px;text-align:center;color:var(--white);font-size:11.5px;line-height:15.5px}
.contact svg{display:block;margin:0 auto 7px}
.contact.address{left:65px}.contact.phone{left:263px}.contact.email{left:460px}
.copyright{position:absolute;left:0;width:726px;top:1144px;text-align:center;color:var(--white);font-size:9px}
.social{position:absolute;left:315px;top:1165px;display:flex;gap:3px}
.social span{width:22px;height:22px;border:1.2px solid var(--white);border-radius:50%}
</style>
</head>
<body>

<div class="hero" role="img" aria-label="Photo of two sandwiches with lettuce, tomato, ham and cheese on a wooden board"></div>
<svg class="hero-edge" viewBox="0 0 726 80" preserveAspectRatio="none" aria-hidden="true">
  <path fill="#ffffff" d="M0,50 L20,38 L34,25 L42,40 L58,30 L74,44 L96,36 L120,46 L150,40 L180,50 L210,44 L250,52 L290,40 L320,24 L332,44 L360,38 L400,48 L440,40 L480,46 L510,36 L540,28 L560,40 L600,22 L630,30 L660,26 L690,40 L726,46 L726,80 L0,80 Z"/>
</svg>

<header class="header">
  <div class="brand">Brambles</div>
  <nav class="nav">
    <a class="active" href="#">Home</a>
    <a href="#">About</a>
    <a href="#">Contact</a>
  </nav>
  <div class="call">
    <svg width="25" height="25" viewBox="0 0 25 25" aria-hidden="true">
      <circle cx="12.5" cy="12.5" r="11.3" fill="none" stroke="var(--pink)" stroke-width="1.5"/>
      <path d="M9 7.5l2 2.5-1.2 1.3c.7 1.5 1.8 2.6 3.3 3.3l1.3-1.2 2.5 2-1.3 1.8c-3.8-.3-7.1-3.6-7.4-7.4z" fill="none" stroke="var(--pink)" stroke-width="1.2" stroke-linejoin="round"/>
    </svg>
    <div><small>Call us Today :</small><strong>+1 888 888 8888</strong></div>
  </div>
</header>

<div class="hero-title">Brambles<br>Cookbook</div>
<svg class="arrow prev" width="30" height="30" viewBox="0 0 30 30" aria-hidden="true"><circle cx="15" cy="15" r="14" fill="none" stroke="#fff" stroke-width="1.5"/><path d="M16.5 11.5L13 15l3.5 3.5" fill="none" stroke="#fff" stroke-width="1.4"/></svg>
<svg class="arrow next" width="30" height="30" viewBox="0 0 30 30" aria-hidden="true"><circle cx="15" cy="15" r="14" fill="none" stroke="#fff" stroke-width="1.5"/><path d="M13.5 11.5L17 15l-3.5 3.5" fill="none" stroke="#fff" stroke-width="1.4"/></svg>

<section class="intro">
  <h1>Brambles <span>Cookbook</span></h1>
  <ul class="points">
    <li>Opening it’s doors in January of 2010, Brambles European Deli was a sandwich shop in Harrowby, Eastvale, but also a lot more than that.</li>
    <li>We spent five years with this business until it’s eventual closure in April of 2015. It was a special time where we met tons of amazing people, who we loved to see and serve.</li>
    <li>Brambles started out as a deli but eventually morphed into the sandwich shop we all know it as today.</li>
    <li>We are overwhelmed with the continuous positive messages and commentswe get on our Chatterbox page that is still up and running.</li>
    <li>Unfortunately, we can’t open another Brambles, but we can offer you this collection of our recipes for you to try out at home with your family and friends.</li>
    <li>We truly hope you will enjoy making these sandwiches just as much as we did.</li>
    <li>If you do, please post your pictures of you making a meal or the finished product, or even enjoying it!</li>
  </ul>
</section>
<a class="buy" href="#">Buy Now</a>

<svg class="book-art" viewBox="420 480 306 400" aria-hidden="false">
  <circle cx="752" cy="698" r="161" fill="var(--pink)"/>
  <defs>
    <linearGradient id="cover" x1="0" y1="0" x2="1" y2="1">
      <stop offset="0" stop-color="#eef4f8"/>
      <stop offset="0.5" stop-color="#d9a070"/>
      <stop offset="1" stop-color="#e6eef2"/>
    </linearGradient>
  </defs>
  <g role="img" aria-label="Cookbook cover showing a sandwich photo">
    <polygon points="664,513 692,534 638,863 606,846" fill="#4a4a4a"/>
    <polygon points="482,519 664,513 606,846 430,838" fill="url(#cover)"/>
  </g>
  <circle cx="484" cy="525" r="35" fill="var(--pink)"/>
  <text x="484" y="533" text-anchor="middle" font-family="Kalam, cursive" font-weight="700" font-size="18" fill="#fff">$29.99</text>
</svg>

<svg class="footer-art" viewBox="0 0 726 1200" aria-hidden="true">
  <path d="M-10,1135 C70,990 230,923 363,923 C496,923 656,990 736,1135 L736,1200 L-10,1200 Z" fill="var(--night)" stroke="var(--pink)" stroke-width="3"/>
</svg>

<div class="footer-brand">Brambles</div>
<div class="contacts">
  <div class="contact address">
    <svg width="50" height="50" viewBox="0 0 50 50" aria-hidden="true"><circle cx="25" cy="25" r="23.5" fill="none" stroke="#fff" stroke-width="1.5"/><circle cx="25" cy="25" r="19" fill="none" stroke="#fff" stroke-width="1.2"/><path d="M25 29s-3.6-4-3.6-6.4a3.6 3.6 0 0 1 7.2 0C28.6 25 25 29 25 29z" fill="var(--pink)"/><circle cx="25" cy="22.6" r="1.2" fill="var(--night)"/></svg>
    123,Lorem ipsum dolor sit amet,<br>consectetur
  </div>
  <div class="contact phone">
    <svg width="50" height="50" viewBox="0 0 50 50" aria-hidden="true"><circle cx="25" cy="25" r="23.5" fill="none" stroke="#fff" stroke-width="1.5"/><circle cx="25" cy="25" r="19" fill="none" stroke="#fff" stroke-width="1.2"/><path d="M21.5 20.5l1.8 2.2-1 1.1c.6 1.3 1.6 2.3 2.9 2.9l1.1-1 2.2 1.8-1.1 1.6c-3.4-.3-6.3-3.2-6.6-6.6z" fill="var(--pink)"/></svg>
    Phone:<br>+1 888 888 8888
  </div>
  <div class="contact email">
    <svg width="50" height="50" viewBox="0 0 50 50" aria-hidden="true"><circle cx="25" cy="25" r="23.5" fill="none" stroke="#fff" stroke-width="1.5"/><circle cx="25" cy="25" r="19" fill="none" stroke="#fff" stroke-width="1.2"/><rect x="19.5" y="21" width="11" height="8" rx="0.8" fill="var(--pink)"/><path d="M19.5 21.5l5.5 4 5.5-4" fill="none" stroke="var(--night)" stroke-width="0.9"/></svg>
    E-mail:<br>info@companyname.com
  </div>
</div>

<div class="copyright">© Copyrights 2022 Company name | All Rights Rserved</div>
<div class="social" aria-label="Social links"><span></span><span></span><span></span><span></span></div>

</body>
</html>
```